Homemaking training schools needs a Business Card design

Designer, Hello!

No special requirements, good-looking enough.
--------------------------------------------------------------------------

Name: Marcus Dole
Chairman
Tel: 0574-71948263
Mobile: 13857420916
Email: kelvora@mailnest.example
Web: www.prt2019.example
Add: No.258, LanpingJie, BeiyuanQu, Ningbo, Zhejiang

LOGO
Ningbo PRT Homemaking Training School

Target Market(s)

pregnant women, mothers, infants, the elderly and families, including cleaning, cooking, nursing training.

Industry/Entity Type

Business

Contact Information for Business Card

Name: Marcus Dole
Chairman
Tel: 0574-71948263
Mobile: 13857420916
Email: kelvora@mailnest.example
Web: www.prt2019.example

LOGO

Font styles to use
Serif
Sans Serif
Decorative

Requirements
Nice to have
• Feels: clean, specifications, safety, comfort, warmth and happiness.

```html
<!DOCTYPE html>
<html lang="en">
<head>
<meta charset="utf-8">
<title>PeiRuiTang Business Card</title>
<link href="https://fonts.googleapis.com/css2?family=PT+Sans:wght@400;700&display=swap" rel="stylesheet">
<style>
  :root {
    --navy: #175079;
    --white: #ffffff;
    --icon-grey: #8f8f8f;
    --backdrop: #ecebe9;
  }
  * { margin: 0; padding: 0; box-sizing: border-box; }
  html, body {
    width: 1200px; height: 1194px; overflow: hidden;
    background: var(--backdrop);
    font-family: "PT Sans", sans-serif;
  }
  .canvas { position: relative; width: 1200px; height: 1194px; }
  .card {
    position: absolute; width: 794px; height: 514px; overflow: hidden;
    box-shadow: 0 4px 14px rgba(0,0,0,0.18);
  }
  .card-front { left: 215px; top: 55px; background: var(--navy); }
  .card-back { left: 214px; top: 622px; background: var(--white); }

  .brand {
    position: absolute; left: 0; right: 0; top: 258px;
    text-align: center; color: var(--white);
    font-weight: 700; font-size: 62px; line-height: 1; letter-spacing: 0.5px;
  }
  .tagline {
    position: absolute; left: 189px; width: 416px; top: 320px;
    display: flex; align-items: center; gap: 10px;
    color: var(--white); font-size: 24px; line-height: 28px; white-space: nowrap;
  }
  .tagline-rule { flex: 1; height: 2px; background: var(--white); }

  .back-art { position: absolute; inset: 0; }
  .holder { position: absolute; left: 83px; top: 82px; color: var(--white); }
  .holder-name { font-weight: 700; font-size: 45px; line-height: 1; letter-spacing: 0.5px; }
  .holder-title { font-weight: 700; font-size: 25px; line-height: 1; margin-top: 6px; }

  .contacts { position: absolute; left: 83px; top: 183px; list-style: none; color: var(--white); }
  .contact { display: flex; align-items: flex-start; font-size: 20px; line-height: 28px; height: 45px; }
  .contact-icon { width: 30px; height: 30px; flex: none; margin-right: 13px; }
  .contact-address { line-height: 27px; padding-left: 4px; }

  .website {
    position: absolute; left: 555px; top: 92px;
    color: var(--navy); font-size: 21px; line-height: 1;
  }
</style>
</head>
<body>
<main class="canvas">
  <section class="card card-front" aria-label="Card front">
    <div class="brand">PeiRuiTang</div>
    <div class="tagline"><span class="tagline-rule"></span><span>Training &amp; Services</span><span class="tagline-rule"></span></div>
  </section>

  <section class="card card-back" aria-label="Card back">
    <svg class="back-art" width="794" height="514" viewBox="0 0 794 514">
      <path fill="var(--navy)" d="M0,0 H443 C484,100 494,230 476,320 C450,420 360,468 260,466 C160,464 60,440 0,406 Z"/>
      <circle cx="510" cy="372" r="46" fill="var(--navy)"/>
      <circle cx="626" cy="456" r="20" fill="var(--navy)"/>
    </svg>

    <div class="holder">
      <div class="holder-name">MARCUS DOLE</div>
      <div class="holder-title">CHAIRMAN</div>
    </div>

    <ul class="contacts">
      <li class="contact">
        <svg class="contact-icon" viewBox="0 0 30 30"><circle cx="15" cy="15" r="15" fill="var(--icon-grey)"/><rect x="11" y="8" width="8" height="14" rx="1.5" fill="var(--white)"/><rect x="12.5" y="10" width="5" height="9" fill="var(--icon-grey)"/></svg>
        <span>13857420916</span>
      </li>
      <li class="contact">
        <svg class="contact-icon" viewBox="0 0 30 30"><circle cx="15" cy="15" r="15" fill="var(--icon-grey)"/><path fill="var(--white)" d="M9,8 L12,7 L14,12 L12,13.5 C13,16 14.5,17.5 16.5,18.5 L18,16.5 L23,18.5 L22,21.5 C15,22 8.5,15 9,8 Z"/></svg>
        <span>0574-71948263</span>
      </li>
      <li class="contact">
        <svg class="contact-icon" viewBox="0 0 30 30"><circle cx="15" cy="15" r="15" fill="var(--icon-grey)"/><rect x="8" y="10" width="14" height="10" rx="1" fill="var(--white)"/></svg>
        <span>kelvora@mailnest.example</span>
      </li>
      <li class="contact">
        <svg class="contact-icon" viewBox="0 0 30 30"><circle cx="15" cy="15" r="15" fill="var(--icon-grey)"/><path fill="var(--white)" d="M15,7 C12,7 10.5,9 10.5,11.5 C10.5,14.5 15,21 15,21 C15,21 19.5,14.5 19.5,11.5 C19.5,9 18,7 15,7 Z"/><circle cx="15" cy="11.5" r="1.7" fill="var(--icon-grey)"/></svg>
        <span class="contact-address">No.258, LanpingJie, BeiyuanQu,<br>Ningbo, Zhejiang</span>
      </li>
    </ul>

    <div class="website">www.prt2019.example</div>
  </section>
</main>
</body>
</html>
```